A clean crisp business card for a Landscape Construction company. Designed to be easy to read contact/ info and also be appealing/interesting, unlike a traditional business card.

Industry/Entity Type

Landscape Construction

Contact Information for Business Card

Company name : Brambleford Landscape Construction, phone number: (877) 62Vista, website:Bramblefordyards.example, Email, sales@bramblefordyards.example

Requirements
Nice to have
• Luxurious finishes/ details…. Icons or emblems next to contact info
Should not have
• Clipart or general pictures

```html
<!DOCTYPE html>
<html lang="en">
<head>
<meta charset="utf-8">
<title>Brambleford Landscape Construction — Business Card</title>
<link rel="stylesheet" href="https://fonts.googleapis.com/css2?family=Cinzel:wght@500;600&family=Open+Sans:wght@400;600&display=swap">
<style>
  :root {
    --backdrop: #dcdfe0;
    --card-dark: #121212;
    --card-light: #ffffff;
    --brand-blue: #2468b8;
    --brand-green: #8cc63f;
    --ink: #1e1e1e;
    --white: #ffffff;
  }
  * { box-sizing: border-box; margin: 0; padding: 0; }
  html, body {
    width: 1200px; height: 928px; overflow: hidden;
    background: var(--backdrop);
  }
  .canvas { position: relative; width: 1200px; height: 928px; }

  .card {
    position: absolute;
    border-radius: 16px;
    overflow: hidden;
  }

  /* Back side */
  .card-back {
    left: 267px; top: 59px; width: 669px; height: 382px;
    background: var(--card-dark);
    text-align: center;
    font-family: "Cinzel", serif;
  }
  .back-wordmark {
    position: absolute; left: 0; right: 0; top: 150px;
    color: var(--brand-green);
    font-weight: 600;
  }
  .back-wordmark .name {
    display: block; font-size: 50px; line-height: 1; letter-spacing: 1px;
  }
  .back-wordmark .tagline {
    display: block; margin-top: 12px; font-size: 18px; letter-spacing: 5px;
  }
  .back-site {
    position: absolute; left: 0; right: 0; top: 332px;
    color: var(--brand-blue);
    font-size: 16px; font-weight: 600; letter-spacing: 2px;
  }

  /* Front side */
  .card-front {
    left: 264px; top: 483px; width: 676px; height: 387px;
    background: var(--card-light);
  }
  .front-rule {
    position: absolute; left: 0; right: 0; top: 302px; height: 4px;
    background: var(--brand-green);
  }
  .front-band {
    position: absolute; left: 0; right: 0; top: 308px; bottom: 0;
    background: var(--brand-blue);
  }

  .front-wordmark {
    position: absolute; left: 40px; top: 110px;
    font-family: "Cinzel", serif; font-weight: 600;
    color: var(--brand-blue);
  }
  .front-wordmark .name { display: block; font-size: 30px; line-height: 1; }
  .front-wordmark .tagline { display: block; margin-top: 5px; font-size: 11px; letter-spacing: 2.6px; }

  .person {
    position: absolute; right: 39px; top: 116px; text-align: right;
  }
  .person .full-name {
    font-family: "Cinzel", serif; font-weight: 600;
    font-size: 28px; color: var(--brand-blue); letter-spacing: 1px;
  }
  .person .role {
    margin-top: 6px;
    font-family: "Open Sans", sans-serif; font-size: 15px; color: var(--ink);
  }

  .contacts {
    position: absolute; left: 41px; top: 212px; list-style: none;
    font-family: "Open Sans", sans-serif; font-size: 15.5px; color: var(--ink);
  }
  .contacts li { display: flex; align-items: center; height: 26px; }
  .contacts svg { width: 17px; height: 17px; margin-right: 7px; flex: none; }

  .address {
    position: absolute; right: 39px; top: 318px; text-align: right;
    font-family: "Open Sans", sans-serif; font-weight: 600;
    font-size: 15px; line-height: 27px; color: var(--white);
  }
</style>
</head>
<body>
<main class="canvas">

  <section class="card card-back" aria-label="Card back">
    <div class="back-wordmark">
      <span class="name">Brambleford</span>
      <span class="tagline">Landscape Construction</span>
    </div>
    <div class="back-site">www.Bramblefordyards.example</div>
  </section>

  <section class="card card-front" aria-label="Card front">
    <div class="front-rule"></div>
    <div class="front-band"></div>

    <div class="front-wordmark">
      <span class="name">Brambleford</span>
      <span class="tagline">Landscape Construction</span>
    </div>

    <div class="person">
      <div class="full-name">Elena Hartwell</div>
      <div class="role">Director</div>
    </div>

    <ul class="contacts">
      <li>
        <svg viewBox="0 0 24 24" aria-hidden="true"><path fill="var(--brand-green)" d="M6.6 10.8a15.1 15.1 0 0 0 6.6 6.6l2.2-2.2c.3-.3.7-.4 1-.2 1.1.4 2.3.6 3.6.6.6 0 1 .4 1 1V20c0 .6-.4 1-1 1A17 17 0 0 1 3 4c0-.6.4-1 1-1h3.5c.6 0 1 .4 1 1 0 1.3.2 2.5.6 3.6.1.3 0 .7-.2 1z"/></svg>
        (877) 62Vista
      </li>
      <li>
        <svg viewBox="0 0 24 24" aria-hidden="true"><rect x="2" y="5" width="20" height="14" rx="1.5" fill="var(--brand-green)"/><path d="M3 6.5l9 6.5 9-6.5" fill="none" stroke="#fff" stroke-width="1.6"/></svg>
        sales@bramblefordyards.example
      </li>
      <li>
        <svg viewBox="0 0 24 24" aria-hidden="true"><circle cx="12" cy="12" r="10" fill="var(--brand-green)"/><path d="M2 12h20M12 2c3 3 3 17 0 20M12 2c-3 3-3 17 0 20" fill="none" stroke="#fff" stroke-width="1.3"/></svg>
        www.bramblefordyards.example
      </li>
    </ul>

    <div class="address">
      4370 Meadowbrook Valley Rd<br>
      NUM 118, Fernhill, OH 45990
    </div>
  </section>

</main>
</body>
</html>
```